Hair salon Business Card

Beauty Salon
I would like to see designs using sky blue and a soft orange. Mainly I would like my name ( Silk & Sky Hair Studio ) used as the design

Industry/Entity Type

Business

Contact Information for Business Card

Silk & Sky Hair Studio
72 Linden Ave #5
Brookvale, Ca 93520
415 555-0182

```html
<!DOCTYPE html>
<html lang="en">
<head>
<meta charset="utf-8">
<title>Silk &amp; Sky Hair Studio – Business Card</title>
<link rel="stylesheet" href="https://fonts.googleapis.com/css2?family=Tenor+Sans&family=Open+Sans:wght@400;600&display=swap">
<style>
  :root {
    --page-bg: #ecebe8;
    --card-dark: #2b2b2c;
    --card-light: #ffffff;
    --brand-blue: #2a5db0;
    --brand-orange: #d4822a;
    --ink-white: #f4f4f4;
  }
  * { margin: 0; padding: 0; box-sizing: border-box; }
  html, body {
    width: 1200px;
    height: 900px;
    overflow: hidden;
    background: var(--page-bg);
  }
  .canvas {
    width: 1200px;
    height: 900px;
    display: flex;
    flex-direction: column;
    align-items: center;
    justify-content: center;
    gap: 40px;
  }
  .card {
    position: relative;
    width: 660px;
    height: 377px;
    border-radius: 4px;
    overflow: hidden;
    box-shadow: 0 6px 18px rgba(0, 0, 0, 0.14);
  }
  .card-front { background: var(--card-dark); }
  .card-back { background: var(--card-light); }

  .brand {
    position: absolute;
    display: flex;
    align-items: center;
    gap: 16px;
    font-family: "Tenor Sans", sans-serif;
    font-weight: 400;
    white-space: nowrap;
  }
  .brand-mark {
    width: 12px;
    height: 12px;
    border-radius: 50%;
  }
  .card-front .brand {
    right: 70px;
    top: 150px;
    font-size: 40px;
    color: var(--ink-white);
  }
  .card-front .brand-mark { background: var(--ink-white); }
  .card-back .brand {
    right: 44px;
    top: 196px;
    font-size: 32px;
    color: var(--brand-blue);
  }
  .card-back .brand-mark { background: var(--brand-blue); }

  .back-shapes {
    position: absolute;
    inset: 0;
    width: 660px;
    height: 377px;
  }
  .contact {
    position: absolute;
    font-family: "Open Sans", sans-serif;
    font-size: 15px;
    font-style: normal;
    color: var(--brand-orange);
    line-height: 1.35;
  }
  .contact-phone {
    left: 32px;
    top: 78px;
    display: flex;
    align-items: center;
    gap: 10px;
  }
  .contact-phone svg { width: 13px; height: 13px; }
  .contact-address {
    left: 32px;
    top: 200px;
  }
</style>
</head>
<body>
<main class="canvas">
  <section class="card card-front" aria-label="Card front">
    <div class="brand"><span class="brand-name">Silk &amp; Sky Hair Studio</span><span class="brand-mark"></span></div>
  </section>

  <section class="card card-back" aria-label="Card back">
    <svg class="back-shapes" viewBox="0 0 660 377" aria-hidden="true">
      <polygon points="0,0 28,0 0,24" fill="var(--brand-blue)"/>
      <polygon points="38,0 70,0 52,24 14,24" fill="var(--brand-orange)"/>
      <polygon points="0,318 230,352 230,377 0,377" fill="var(--brand-blue)"/>
      <polygon points="238,352 660,352 660,377 238,377" fill="var(--brand-orange)"/>
    </svg>

    <div class="contact contact-phone">
      <svg viewBox="0 0 24 24" aria-hidden="true"><path fill="var(--brand-blue)" d="M6.6 10.8a15.1 15.1 0 0 0 6.6 6.6l2.2-2.2a1 1 0 0 1 1-.25 11.4 11.4 0 0 0 3.6.57 1 1 0 0 1 1 1V20a1 1 0 0 1-1 1A17 17 0 0 1 3 4a1 1 0 0 1 1-1h3.5a1 1 0 0 1 1 1c0 1.25.2 2.45.57 3.6a1 1 0 0 1-.25 1z"/></svg>
      <span>415 555-0182</span>
    </div>

    <address class="contact contact-address">
      72 Linden Ave #5<br>
      Brookvale, Ca 93520
    </address>

    <div class="brand"><span class="brand-name">Silk &amp; Sky Hair Studio</span><span class="brand-mark"></span></div>
  </section>
</main>
</body>
</html>
```